Veldmark Supplies Business Card

Professional business card that stand out to our potential customers. Front and back with clean modern design

Industry/Entity Type

Oil and gas

Contact Information for Business Card

Name, address, website , office phone and cell number

Requirements
Must have
• Editable files for each employee

```html
<!DOCTYPE html>
<html lang="en">
<head>
<meta charset="utf-8">
<title>Veldmark Supplies Business Card</title>
<link rel="stylesheet" href="https://fonts.googleapis.com/css2?family=Montserrat:wght@400;500;700;800&display=swap">
<style>
  :root {
    --backdrop: #2b2b2b;
    --card-blue: #0bb0d2;
    --card-blue-deep: #0a94b2;
    --card-white: #ffffff;
    --brand-red: #e8232a;
    --brand-blue: #17a8d4;
    --ink: #1d1d1f;
    --ink-soft: #555a60;
  }
  * { box-sizing: border-box; margin: 0; padding: 0; }
  html, body {
    width: 1200px;
    height: 875px;
    overflow: hidden;
    background: var(--backdrop);
    font-family: "Montserrat", sans-serif;
  }
  .canvas {
    position: relative;
    width: 1200px;
    height: 875px;
    display: flex;
    align-items: center;
    justify-content: center;
    gap: 40px;
  }
  .card {
    position: relative;
    width: 520px;
    height: 297px;
    border-radius: 18px;
    overflow: hidden;
    box-shadow: 0 18px 40px rgba(0, 0, 0, 0.45);
  }

  /* Back side */
  .card-back {
    background: var(--card-blue);
    display: flex;
    align-items: center;
    justify-content: center;
  }
  .back-brand {
    display: flex;
    align-items: center;
    gap: 12px;
    font-weight: 800;
    font-size: 30px;
    letter-spacing: 2px;
    text-transform: uppercase;
    color: var(--card-blue-deep);
  }
  .back-brand .mark-square {
    width: 22px;
    height: 22px;
    background: var(--card-blue-deep);
  }

  /* Front side */
  .card-front {
    background: var(--card-white);
  }
  .front-brand {
    position: absolute;
    left: 44px;
    top: 66px;
    font-weight: 800;
    font-size: 24px;
    letter-spacing: 1.5px;
    text-transform: uppercase;
    color: var(--brand-red);
  }
  .person {
    position: absolute;
    left: 44px;
    top: 128px;
    width: 170px;
    text-align: right;
  }
  .person-name {
    font-weight: 700;
    font-size: 22px;
    color: var(--brand-red);
    line-height: 1.1;
  }
  .person-role {
    font-weight: 500;
    font-size: 12px;
    color: var(--ink-soft);
    margin-top: 4px;
  }
  .divider {
    position: absolute;
    left: 228px;
    top: 116px;
    width: 1.5px;
    height: 80px;
    background: var(--brand-red);
  }
  .contact-list {
    position: absolute;
    left: 244px;
    top: 112px;
    list-style: none;
  }
  .contact-list li {
    display: flex;
    align-items: center;
    gap: 8px;
    font-size: 11.5px;
    font-weight: 500;
    color: var(--ink);
    line-height: 21px;
  }
  .contact-list svg {
    width: 11px;
    height: 11px;
    fill: var(--brand-blue);
    flex: none;
  }
  .address {
    position: absolute;
    left: 44px;
    bottom: 34px;
    font-size: 12px;
    font-weight: 500;
    color: var(--ink);
  }
</style>
</head>
<body>
  <main class="canvas">
    <section class="card card-back" aria-label="Card back">
      <div class="back-brand">
        <span class="mark-square"></span>
        <span>Veldmark Supplies</span>
      </div>
    </section>

    <section class="card card-front" aria-label="Card front">
      <div class="front-brand">Veldmark Supplies</div>

      <div class="person">
        <div class="person-name">Tarek Holloway</div>
        <div class="person-role">President</div>
      </div>

      <div class="divider"></div>

      <ul class="contact-list">
        <li>
          <svg viewBox="0 0 24 24" aria-hidden="true"><path d="M3 8c0-3 4-5 9-5s9 2 9 5v2h-5V8H8v2H3zM5 12h14l2 9H3z"/></svg>
          +1.555.310.4400 x123
        </li>
        <li>
          <svg viewBox="0 0 24 24" aria-hidden="true"><path d="M6.6 10.8a15 15 0 0 0 6.6 6.6l2.2-2.2c.3-.3.7-.4 1-.2 1.1.4 2.3.6 3.6.6.6 0 1 .4 1 1V20c0 .6-.4 1-1 1A17 17 0 0 1 3 4c0-.6.4-1 1-1h3.5c.6 0 1 .4 1 1 0 1.3.2 2.5.6 3.6.1.3 0 .7-.2 1z"/></svg>
          +1.555.208.773
        </li>
        <li>
          <svg viewBox="0 0 24 24" aria-hidden="true"><path d="M2 5h20v14H2zm2 2v.5l8 5 8-5V7z"/></svg>
          info@veldmarksupplies.com
        </li>
        <li>
          <svg viewBox="0 0 24 24" aria-hidden="true"><path d="M12 2a10 10 0 1 0 0 20 10 10 0 0 0 0-20zm6.9 9h-3a15 15 0 0 0-1.4-6A8 8 0 0 1 18.9 11zM12 4c.9 1.3 1.7 3.9 1.9 7h-3.8C10.3 7.9 11.1 5.3 12 4zM9.5 5a15 15 0 0 0-1.4 6h-3A8 8 0 0 1 9.5 5zM5.1 13h3a15 15 0 0 0 1.4 6 8 8 0 0 1-4.4-6zm5 0h3.8c-.2 3.1-1 5.7-1.9 7-.9-1.3-1.7-3.9-1.9-7zm4.4 6a15 15 0 0 0 1.4-6h3a8 8 0 0 1-4.4 6z"/></svg>
          www.veldmarksupplies.com
        </li>
      </ul>

      <div class="address">42 Ridgeway Court Halden, TX 79701 USA</div>
    </section>
  </main>
</body>
</html>
```